PixelMarrow Inc. Website & iPhone Apps Landing Pages

We need a web site design for our company. We develop software and do various consultant projects for our clients. Our products focus on the mobile platform, mainly the iPhone (business, games, social, etc.). We want to communicate that our software is simple and good as candy. The web pages should be fun to look at not loosing seriousness and credibility. Web 2.0 style and 960 grid system a must. We are opened to any overall site colour scheme suggestions (look at the sites we like below).

Must haves:
- Our logo should be seen on the site and look great on it :-) (preview attached below)
- Main home page and app landing page.
- Section links/tabs on the home page (home,apps,support,blog,contact,about)
- No text in images
- Style sheet

Looks we like:
- http://k7q3vxp9lrtwz.examplecdn.net/441_Site_Mock/final_large.jpg
- http://k7q3vxp9lrtwz.examplecdn.net/Deluxe_71_Drawn_Phone_Landing_Page/final.jpg
- http://grenmoor.com/
- http://lumbrel.ca/
- http://fairtwig.com/

Industry/Entity Type

Business

Requirements
Must have
• - Company logo should look great on pages.
• - Main home page and app landing page.
• - Section links/tabs on the home page (home,apps,support,blog,contact,about)
• - Web 2.0 style.
• - 960 grid system (12 col, 16 col).
• - Sliced ann optmized
• - Exported in all major formats (psd,ai,eps,png,jpeg,etc)
• - Style sheet
Should not have
• - Text in images

```html
<!DOCTYPE html>
<html lang="en">
<head>
<meta charset="utf-8">
<title>PixelMarrow Inc.</title>
<link href="https://fonts.googleapis.com/css2?family=Arimo:wght@400;700&display=swap" rel="stylesheet">
<style>
  :root {
    --bar-darker: #2b2c2e;
    --hero-top: #34455c;
    --hero-bottom: #1c2636;
    --red: #d3151b;
    --text: #444;
    --text-soft: #555;
    --panel: #f1f1f1;
    --white: #fff;
    --muted: #9a9a9a;
  }
  * { box-sizing: border-box; margin: 0; padding: 0; }
  html, body { width: 1147px; height: 1200px; overflow: hidden; }
  body {
    position: relative;
    background: var(--white);
    font-family: "Arimo", Arial, sans-serif;
    color: var(--text);
  }
  h1, h2 { font-weight: 400; }

  /* Header */
  .site-header {
    position: absolute; left: 0; top: 0; width: 1147px; height: 77px;
    background: linear-gradient(#46474a, var(--bar-darker));
  }
  .brand {
    position: absolute; left: 129px; top: 18px;
    display: flex; align-items: center; gap: 10px;
    font-size: 36px; color: var(--white); font-weight: 400; letter-spacing: 0.5px;
  }
  .brand-dot { width: 16px; height: 16px; border-radius: 50%; background: var(--red); }
  .header-contact {
    position: absolute; left: 815px; top: 23px;
    color: var(--white); font-weight: 700; font-size: 14px; line-height: 17px;
  }

  /* Hero */
  .hero {
    position: absolute; left: 0; top: 77px; width: 1147px; height: 417px;
    background: radial-gradient(ellipse at 60% 40%, var(--hero-top), var(--hero-bottom) 75%);
  }
  .hero-title {
    position: absolute; left: 129px; top: 80px;
    font-size: 36px; color: var(--white);
  }
  .hero-rule { position: absolute; left: 129px; top: 130px; width: 367px; height: 1px; background: rgba(255,255,255,0.5); }
  .hero-text {
    position: absolute; left: 129px; top: 151px; width: 390px;
    font-size: 12.2px; line-height: 16.6px; color: var(--white);
  }
  .btn-red {
    position: absolute; display: flex; align-items: center; justify-content: center;
    background: linear-gradient(#e8242a, var(--red) 50%, #b5100f);
    color: var(--white); border-radius: 3px;
    box-shadow: 2px 2px 0 rgba(0,0,0,0.45);
  }
  .hero-more { left: 391px; top: 256px; width: 117px; height: 34px; font-size: 19px; }
  .hero-dots { position: absolute; left: 136px; top: 306px; display: flex; gap: 5px; }
  .hero-dots span { width: 8px; height: 8px; border-radius: 50%; background: #8a93a0; }
  .hero-dots span:first-child { background: var(--white); }
  .hero-device {
    position: absolute; left: 750px; top: 22px; width: 185px; height: 300px;
    border-radius: 22px;
    background: linear-gradient(90deg, #0e0f12, #3b3f46 60%, #17191d);
  }

  /* Navigation */
  .main-nav {
    position: absolute; left: 129px; top: 433px; width: 877px; height: 61px;
    background: linear-gradient(#6a6b6e, #3e3f42);
    border: 1px solid #727376; border-bottom: none;
    border-radius: 3px 3px 0 0;
  }
  .nav-item {
    position: absolute; top: 0; height: 60px; display: flex; align-items: center; justify-content: center;
    color: var(--white); font-size: 16px;
  }
  .nav-item.is-active { font-weight: 700; }
  .nav-sep { position: absolute; top: 4px; width: 2px; height: 52px; border-left: 1px solid #2e2f31; border-right: 1px solid #7b7c7f; }

  /* Content */
  .content-panel {
    position: absolute; left: 129px; top: 494px; width: 877px; height: 560px;
    background: linear-gradient(var(--panel), #fafafa 60%, var(--white));
  }
  .sidebar {
    position: absolute; left: 129px; top: 531px; width: 231px; height: 523px;
    background: linear-gradient(90deg, #4f5052, #8c8d8f 55%, #c9c9ca);
  }
  .btn-big { width: 192px; height: 52px; font-size: 24px; font-weight: 700; left: 145px; border-radius: 2px; }
  .signup-note { position: absolute; left: 149px; top: 615px; font-size: 11px; color: var(--white); }
  .signup-note u { color: var(--white); }

  .contact-box {
    position: absolute; left: 145px; top: 731px; width: 192px; height: 239px;
    background: #3b3b3c; border-radius: 4px;
  }
  .contact-title { position: absolute; left: 10px; top: 10px; font-size: 16px; color: var(--white); }
  .field {
    position: absolute; left: 6px; width: 180px; height: 18px;
    background: var(--white); border: 1px solid #999;
    font-size: 10.5px; color: #666; padding: 2px 3px;
  }
  .submit {
    position: absolute; left: 58px; top: 208px; width: 68px; height: 21px;
    background: linear-gradient(#f4f4f4, #c9c9c9); border: 1px solid #888;
    font-size: 11.5px; color: #222; display: flex; align-items: center; justify-content: center;
  }

  .article { position: absolute; left: 377px; width: 607px; }
  .article-title { font-size: 17px; color: var(--text); }
  .article-text {
    margin-top: 13px; font-size: 10.9px; line-height: 16.4px; color: var(--text-soft); text-align: justify;
  }
  .btn-small { width: 75px; height: 22px; font-size: 10.5px; left: 907px; }
  .panel-shadow { position: absolute; top: 1054px; height: 4px; background: linear-gradient(rgba(0,0,0,0.12), transparent); }

  /* Footer */
  .site-footer {
    position: absolute; left: 0; top: 1074px; width: 1147px; height: 126px;
    background: linear-gradient(#48494b, #333436);
  }
  .footer-brand { left: 129px; top: 42px; font-size: 30px; }
  .social { position: absolute; left: 800px; top: 27px; display: flex; gap: 16px; }
  .social span { width: 27px; height: 27px; border-radius: 4px; }
  .copyright { position: absolute; right: 140px; top: 95px; font-size: 11px; color: var(--muted); }
</style>
</head>
<body>

<header class="site-header">
  <div class="brand"><span class="brand-dot"></span>PixelMarrow</div>
  <div class="header-contact">Call Us: 480-555-0172<br>Email:info@pixelmarrow.com</div>
</header>

<section class="hero">
  <h1 class="hero-title">Stylish applications</h1>
  <div class="hero-rule"></div>
  <p class="hero-text">It is a long established fact that a reader will be distracted by the readable content of a page when looking at its layout. The point of using Lorem Ipsum is that it has a more-or-less normal distribution of letters, as opposed to using 'Content here, content here', making it look like readable English.</p>
  <span class="btn-red hero-more">More info</span>
  <div class="hero-dots"><span></span><span></span><span></span><span></span></div>
  <div class="hero-device" role="img" aria-label="Smartphone showing the app home screen"></div>
</section>

<nav class="main-nav">
  <span class="nav-item is-active" style="left:0;width:119px">Home</span>
  <span class="nav-sep" style="left:118px"></span>
  <span class="nav-item" style="left:120px;width:127px">Portfolio</span>
  <span class="nav-sep" style="left:247px"></span>
  <span class="nav-item" style="left:249px;width:103px">Blog</span>
  <span class="nav-sep" style="left:351px"></span>
  <span class="nav-item" style="left:353px;width:134px">Services</span>
  <span class="nav-sep" style="left:486px"></span>
  <span class="nav-item" style="left:488px;width:136px">About Us</span>
  <span class="nav-sep" style="left:624px"></span>
  <span class="nav-item" style="left:626px;width:250px;justify-content:flex-start;padding-left:38px">Contact Us</span>
</nav>

<main>
  <div class="content-panel"></div>

  <aside class="sidebar"></aside>
  <span class="btn-red btn-big" style="top:556px">Login In</span>
  <p class="signup-note">For new Account <u>Sign-Up</u></p>
  <span class="btn-red btn-big" style="top:652px">Download</span>

  <form class="contact-box">
    <h2 class="contact-title">Contact Us</h2>
    <div class="field" style="top:44px">Name:</div>
    <div class="field" style="top:65px">Email:</div>
    <div class="field" style="top:88px">Phone:</div>
    <div class="field" style="top:109px;height:80px">Message:</div>
    <span class="submit">Submit</span>
  </form>

  <article class="article" style="top:539px">
    <h2 class="article-title">Finance Management</h2>
    <p class="article-text">It is a long established fact that a reader will be distracted by the readable content of a page when looking at its layout. The point of using Lorem Ipsum is that it has a more-or-less normal distribution of letters, as opposed to using 'Content here, content here', making it look like readable English. It is a long established fact that a reader will be distracted by the readable content of a page when looking at its layout.</p>
  </article>
  <span class="btn-red btn-small" style="top:640px">Read More</span>

  <article class="article" style="top:679px">
    <h2 class="article-title">Reliable application</h2>
    <p class="article-text">It is a long established fact that a reader will be distracted by the readable content of a page when looking at its layout. The point of using Lorem Ipsum is that it has a more-or-less normal distribution of letters, as opposed to using 'Content here, content here', making it look like readable English. It is a long established fact that a reader will be distracted by the readable content of a page when looking at its layout.</p>
  </article>
  <span class="btn-red btn-small" style="top:775px">Read More</span>

  <article class="article" style="top:808px">
    <h2 class="article-title">Market analytics</h2>
    <p class="article-text">It is a long established fact that a reader will be distracted by the readable content of a page when looking at its layout. The point of using Lorem Ipsum is that it has a more-or-less normal distribution of letters, as opposed to using 'Content here, content here', making it look like readable English. It is a long established fact that a reader will be distracted by the readable content of a page when looking at its layout.</p>
  </article>
  <span class="btn-red btn-small" style="top:904px">Read More</span>

  <article class="article" style="top:937px">
    <h2 class="article-title">Visitor trending</h2>
    <p class="article-text">It is a long established fact that a reader will be distracted by the readable content of a page when looking at its layout. The point of using Lorem Ipsum is that it has a more-or-less normal distribution of letters, as opposed to using 'Content here, content here', making it look like readable English. It is a long established fact that a reader will be distracted by the readable content of a page when looking at its layout.</p>
  </article>
  <span class="btn-red btn-small" style="top:1027px">Read More</span>

  <div class="panel-shadow" style="left:129px;width:231px"></div>
  <div class="panel-shadow" style="left:380px;width:626px"></div>
</main>

<footer class="site-footer">
  <div class="brand footer-brand"><span class="brand-dot"></span>PixelMarrow</div>
  <div class="social">
    <span style="background:#3b5a9a"></span>
    <span style="background:#4aa8d8"></span>
    <span style="background:#f08a24"></span>
    <span style="background:#2a7cb0"></span>
    <span style="background:#e8e8e8"></span>
  </div>
  <p class="copyright">Copyright © 2010 PixelMarrow. All Rights reserved</p>
</footer>

</body>
</html>
```